Tamsorellium we are a young innovative brand about making life easier for people with a disability

Our tag line is Making Life Easy, we are still a relatively new company trying to bring innovation and excitement into the disability space - with latest products and technology - we do have existing website but need to unpgrade for a stronger visual presence.

```html
<!DOCTYPE html>
<html lang="en">
<head>
<meta charset="utf-8">
<title>Tamsorellium — Making Life Easy</title>
<link href="https://fonts.googleapis.com/css2?family=Kanit:ital,wght@1,800&family=Poppins:ital,wght@0,400;0,500;0,600;1,400&display=swap" rel="stylesheet">
<style>
:root{
  --red:#d10000;
  --red-deep:#c20000;
  --red-soft:#cc3333;
  --ink:#222;
  --muted:#555;
  --pale:#f4f4f4;
  --white:#fff;
  --black:#000;
  --star:#f2b01e;
}
*{box-sizing:border-box;margin:0;padding:0}
html,body{width:1200px;height:4131px;overflow:hidden}
body{position:relative;font-family:"Poppins",sans-serif;color:var(--ink);background:var(--white)}
.abs{position:absolute}
.band{position:absolute;left:0;width:1200px}
.display{font-family:"Kanit",sans-serif;font-style:italic;font-weight:800;color:var(--red);text-transform:uppercase;letter-spacing:1px}
.btn{position:absolute;display:flex;align-items:center;justify-content:center;background:var(--red);color:var(--white);font-size:17px;text-decoration:none}

/* header */
.brand{left:88px;top:50px;display:flex;align-items:center;gap:10px}
.brand-dot{width:52px;height:52px;border-radius:50%;background:var(--red)}
.brand-name{font-weight:600;font-size:22px;color:var(--red)}
.nav a{position:absolute;top:64px;font-size:15px;color:var(--ink);text-decoration:none}
.nav a.active{color:var(--red);font-size:18px;font-weight:500;top:61px}
.nav a.btn{top:58px;left:995px;width:117px;height:38px;font-size:15px;color:var(--white)}

/* hero */
.hero{top:152px;height:563px;background:var(--pale)}
.hero h1{position:absolute;left:88px;top:150px;font-size:62px;line-height:1}
.hero p{position:absolute;left:88px;top:258px;width:620px;font-size:15px;line-height:21px}
.hero .btn{left:88px;top:353px;width:178px;height:51px}
.media{position:absolute}

/* section heads */
.head{position:absolute;left:0;width:1200px;text-align:center}
.head h2{font-size:40px;line-height:1}
.head .sub{display:inline-flex;align-items:center;gap:20px;font-size:26px;letter-spacing:3px;text-transform:uppercase;margin-top:2px}
.head .sub::before,.head .sub::after{content:"";width:154px;height:3px;background:var(--ink)}

/* about */
.about-text{position:absolute;left:580px;top:960px;width:520px;font-size:17.5px;line-height:25px}
.about-text p+p{margin-top:25px}

/* products */
.products{top:1453px;height:1037px;background:var(--pale)}
.tab{position:absolute;top:215px;height:49px;width:179px;border:2px solid var(--red);display:flex;align-items:center;justify-content:center;font-size:17px;color:#333;background:var(--white)}
.tab.active{background:var(--red);color:var(--white)}
.tile{position:absolute;width:343px;height:257px;background:var(--white);box-shadow:0 1px 3px rgba(0,0,0,.08);display:flex;align-items:center;justify-content:center}
.tile .media{position:static;width:230px;height:210px;border-radius:6px;background:linear-gradient(135deg,#e8e8e8,#bdbdbd)}
.tile.hover{background:var(--red-soft)}
.tile.hover .media{position:absolute;opacity:.25}
.know{position:relative;border:2px solid var(--white);color:var(--white);font-size:17px;padding:8px 26px}

/* cta */
.cta{left:89px;top:2588px;width:1022px;height:269px;border-radius:16px;background:linear-gradient(120deg,#3a3a2c,#1b1b1b 55%,#2c2c2c);display:flex;flex-direction:column;align-items:center;justify-content:center;color:var(--white)}
.cta p{font-size:26px;line-height:34px;text-align:center;margin-top:-10px}
.cta .ghost{margin-top:22px;width:222px;height:53px;border:2px solid var(--white);display:flex;align-items:center;justify-content:center;font-size:18px}

/* testimonials */
.testimonials{top:2950px;height:670px;background:#f7f7f7}
.card{position:absolute;top:3215px;width:498px;height:268px;background:var(--white)}
.stars{position:absolute;left:66px;top:26px;color:var(--star);font-size:26px;letter-spacing:1px}
.who{position:absolute;left:66px;top:66px;font-size:21px;color:var(--red);font-weight:500}
.role{position:absolute;left:66px;top:96px;font-style:italic;font-size:17px;color:#444}
.quote{position:absolute;left:66px;top:136px;width:350px;font-size:15px;line-height:24px;color:#444}
.avatar{position:absolute;top:-12px;left:339px;width:114px;height:114px;border-radius:50%}

/* footer */
.footer{top:3620px;height:392px;background:var(--red-deep);color:var(--white)}
.col{position:absolute;top:86px}
.col h3{font-size:21px;font-weight:600}
.col h3::after{content:"";display:block;width:40px;height:3px;background:var(--white);margin-top:12px}
.col ul{list-style:none;margin-top:26px}
.col li{font-size:15px;height:31px;display:flex;align-items:center;gap:12px}
.col li::before{content:"›";font-size:20px;line-height:1}
.col .note{font-size:15px;line-height:20px;margin-top:24px;width:260px}
.field{width:251px;height:39px;background:var(--white);margin-top:18px}
.subscribe{margin-top:14px;width:126px;height:36px;background:#ff1f1f;font-size:13px;display:flex;align-items:center;justify-content:center}
.bottom{top:4012px;height:119px;background:var(--black);color:var(--white)}
.social{position:absolute;top:42px;width:40px;height:40px;border:2px solid var(--white);border-radius:50%}
.copy{position:absolute;right:82px;top:50px;font-size:18px}
</style>
</head>
<body>

<header>
  <div class="abs brand"><span class="brand-dot"></span><span class="brand-name">Tamsorellium</span></div>
  <nav class="nav">
    <a class="active" style="left:505px" href="#">Home</a>
    <a style="left:585px" href="#">About Us</a>
    <a style="left:678px" href="#">Our Services</a>
    <a style="left:799px" href="#">blogs</a>
    <a style="left:866px" href="#">Testimonials</a>
    <a class="btn" href="#">Contact Us</a>
  </nav>
</header>

<section class="band hero">
  <h1 class="display">Making Life Easy</h1>
  <p>We are still a relatively new company trying to bring innovation and excitement into the disability space with latest products and technology.</p>
  <a class="btn" href="#">Read More</a>
  <div class="media" role="img" aria-label="Black and red four-wheel mobility scooter" style="left:730px;top:35px;width:390px;height:465px;border-radius:12px;background:linear-gradient(160deg,#e6e6e6,#9a9a9a 60%,#6a6a6a)"></div>
</section>

<section>
  <div class="head" style="top:805px">
    <h2 class="display">About Our Company</h2>
    <div class="sub">Who We Are</div>
  </div>
  <div class="media" role="img" aria-label="Tilt-in-space wheelchair with yellow frame in front of a red ring" style="left:97px;top:893px;width:417px;height:455px;border-radius:12px;background:linear-gradient(145deg,#f2d4d4,#e2e2e2 55%,#bdbdbd)"></div>
  <div class="about-text">
    <p>Tamsorellium provides manual wheelchairs for sale and any other wheelchairs in a range of sizes, designs, price points, and combinations to suit your needs. You can choose from different types of wheelchairs depending on your needs, whether it’s an active, standard, sport, or paediatric wheelchair.</p>
    <p>Tamsorellium offers wheelchairs for everyone. We sell and rent manual and power wheelchairs as well as wheelchair accessories.</p>
    <p>You can also choose manual wheelchairs for sale that’s easy to use, from folding wheelchairs to rigid wheelchairs that tilt in space.</p>
  </div>
</section>

<section class="band products">
  <div class="head" style="top:92px">
    <h2 class="display">Products For Sale</h2>
    <div class="sub">All Products</div>
  </div>
  <div class="tab active" style="left:104px">WHEELCHAIRS</div>
  <div class="tab" style="left:309px">PARTS</div>
  <div class="tab" style="left:516px">ACCESORIES</div>
  <div class="tab" style="left:713px">BARGAIN CENTER</div>
  <div class="tab" style="left:919px">SCOOTERS</div>

  <div class="tile" style="left:80px;top:324px"><div class="media" role="img" aria-label="Black rigid manual wheelchair"></div></div>
  <div class="tile" style="left:429px;top:324px"><div class="media" role="img" aria-label="Reclining wheelchair with headrest"></div></div>
  <div class="tile" style="left:778px;top:324px"><div class="media" role="img" aria-label="Red-framed sport wheelchair"></div></div>
  <div class="tile" style="left:80px;top:598px"><div class="media" role="img" aria-label="Tilt wheelchair with yellow frame"></div></div>
  <div class="tile hover" style="left:429px;top:598px"><div class="media" role="img" aria-label="Hand-cycle wheelchair attachment"></div><span class="know">Know More</span></div>
  <div class="tile" style="left:778px;top:598px"><div class="media" role="img" aria-label="Lightweight folding wheelchair"></div></div>

  <a class="btn" href="#" style="left:510px;top:905px;width:180px;height:52px">VIEW ALL</a>
</section>

<section>
  <div class="abs cta" role="img" aria-label="Dark banner showing bicycle and wheelchair wheels outdoors">
    <p>Are you looking for the perfect wheelchairs for sale<br>that suits your lifestyle?</p>
    <div class="ghost">Get A Quote</div>
  </div>
</section>

<section class="band testimonials">
  <div class="head" style="top:97px">
    <h2 class="display">What The Client Says</h2>
    <div class="sub">Testimonials</div>
  </div>
</section>
<div class="card" style="left:100px">
  <div class="stars">★★★★★</div>
  <div class="who">Corin Vale</div>
  <div class="role">Organiser</div>
  <p class="quote">Lorem ipsum dolor sit amet, conse tetur adipiscing elit, sed do eiusmod tempor vel facilisis.</p>
  <div class="avatar" role="img" aria-label="Client portrait" style="background:linear-gradient(#f5b020,#e89a10)"></div>
</div>
<div class="card" style="left:615px">
  <div class="stars">★★★★★</div>
  <div class="who">Idris Marlo</div>
  <div class="role">Organiser</div>
  <p class="quote">Lorem ipsum dolor sit amet, conse tetur adipiscing elit, sed do eiusmod tempor maecenas vel facilisis.</p>
  <div class="avatar" role="img" aria-label="Client portrait" style="left:342px;top:-14px;background:linear-gradient(#8fb3c4,#6e95a8)"></div>
</div>
<a class="btn" href="#" style="left:517px;top:3507px;width:180px;height:51px">VIEW ALL</a>

<footer>
  <div class="band footer">
    <div class="col" style="left:214px">
      <h3>Quick Links</h3>
      <ul><li>Home</li><li>About Us</li><li>Our Services</li><li>Our Blogs</li><li>Testimonials</li></ul>
    </div>
    <div class="col" style="left:497px">
      <h3>Customer Services</h3>
      <ul><li>Contact us</li><li>Site Map</li><li>Terms and Use</li><li>My Account</li></ul>
    </div>
    <div class="col" style="left:764px;top:84px">
      <h3>Our Newsletter</h3>
      <p class="note">Subscribe our newsletter to get the latest news.</p>
      <div class="field"></div>
      <div class="subscribe">SUBSCRIBE</div>
    </div>
  </div>
  <div class="band bottom">
    <span class="social" style="left:96px" aria-label="Video channel"></span>
    <span class="social" style="left:147px" aria-label="Social page"></span>
    <span class="social" style="left:198px" aria-label="Social feed"></span>
    <span class="social" style="left:250px" aria-label="Photo profile"></span>
    <div class="copy">All Rights Reserved @ Copyrights 2023</div>
  </div>
</footer>

</body>
</html>
```